New business card/stationary for a consulting company

I am looking for a clean and very professional looking business card for my consulting company as well as corresponding stationary. I am uploading our logo. I like simple and powerful for the feel. No graphics but I am open on everything else. Below is my contact information but would like the final to be in a version I can add my employees information into and print. Thank you.

Daniel Whitcombe
dan@ferncliffadvisory.com
2870 North 9th Avenue, Summit Floor, Elm Ridge, Illinois 60531
www.ferncliffadvisory.com

Industry/Entity Type

Consulting

Contact Information for Business Card

Daniel Whitcombe
dan@ferncliffadvisory.com
www.ferncliffadvisory.com

Font styles to use
Serif
Sans Serif

Requirements
Must have
• Our logo and the business card details.
Nice to have
• our website www.ferncliffadvisory.com

```html
<!DOCTYPE html>
<html lang="en">
<head>
<meta charset="utf-8">
<title>Ferncliff Advisory — Business Card</title>
<link rel="stylesheet" href="https://fonts.googleapis.com/css2?family=Cinzel:wght@700&family=Raleway:wght@300&family=Roboto:wght@400;700&display=swap">
<style>
  :root {
    --page-bg: #d9d9dc;
    --navy-deep: #15173f;
    --navy-mid: #262a66;
    --navy-glow: #3a3f86;
    --silver-light: #eeeef0;
    --silver-mid: #d3d3d7;
    --gold-rule: #b9a36a;
    --ink-navy: #232653;
    --ink-grey: #4a4a52;
    --ink-dark: #1c1c22;
    --logo-silver: #d8d8de;
  }
  * { margin: 0; padding: 0; box-sizing: border-box; }
  html, body {
    width: 1200px;
    height: 969px;
    overflow: hidden;
    background: var(--page-bg);
  }
  .card {
    position: absolute;
    left: 100px;
    top: 200px;
    width: 1000px;
    height: 570px;
    background: linear-gradient(180deg, var(--silver-light), var(--silver-mid));
    box-shadow: 0 10px 30px rgba(0,0,0,0.18);
    overflow: hidden;
  }
  .brand-band {
    position: absolute;
    left: 0; top: 0;
    width: 100%;
    height: 318px;
    background:
      radial-gradient(ellipse 45% 90% at 52% 40%, var(--navy-glow) 0%, rgba(58,63,134,0) 70%),
      linear-gradient(90deg, var(--navy-deep), var(--navy-mid) 50%, var(--navy-deep));
    border-bottom: 4px solid var(--gold-rule);
  }
  .brand-mark {
    position: absolute;
    left: 0; right: 0;
    top: 205px;
    display: flex;
    justify-content: center;
    align-items: center;
    gap: 22px;
  }
  .brand-square {
    width: 34px;
    height: 34px;
    background: var(--logo-silver);
  }
  .brand-name {
    font-family: "Raleway", sans-serif;
    font-weight: 300;
    font-size: 42px;
    letter-spacing: 2px;
    color: var(--logo-silver);
    line-height: 1;
  }
  .person {
    position: absolute;
    left: 69px;
    top: 392px;
    width: 370px;
    text-align: right;
  }
  .person-name {
    font-family: "Cinzel", serif;
    font-weight: 700;
    font-size: 31px;
    color: var(--ink-navy);
    letter-spacing: 1px;
    line-height: 1.2;
  }
  .person-email {
    font-family: "Roboto", sans-serif;
    font-size: 23px;
    color: var(--ink-grey);
    line-height: 1.4;
  }
  .office {
    position: absolute;
    left: 482px;
    top: 400px;
    font-family: "Roboto", sans-serif;
    font-size: 24px;
    color: var(--ink-dark);
    line-height: 30px;
  }
  .office-web {
    font-weight: 700;
    letter-spacing: 0.5px;
  }
</style>
</head>
<body>
  <div class="card">
    <div class="brand-band">
      <div class="brand-mark">
        <span class="brand-square"></span>
        <span class="brand-name">FERNCLIFF ADVISORY</span>
      </div>
    </div>
    <div class="person">
      <div class="person-name">Daniel Whitcombe</div>
      <div class="person-email">dan@ferncliffadvisory.com</div>
    </div>
    <div class="office">
      <div class="office-line">2870 North 9th Avenue</div>
      <div class="office-line">Summit Floor, Elm Ridge, Illinois 60531</div>
      <div class="office-web">FERNCLIFFADVISORY.COM</div>
    </div>
  </div>
</body>
</html>
```